Anzeige zur Kundenakquise
Zielgruppe
Wir sind der größte unabhängige Versicherungsmakler Deutschlands.
https://www.ostwind-policenrunde.de/
Aufgabenstellung
Die Anzeige dient zur Kundenakquise. Der Flyer soll in erster Linie auf Plauderwiese veröffentlicht werden.
Sie soll Kunden anregen eine Nachricht an uns zu schicken und einen Termin bis zum 30.11.2018 zu vereinbaren um ihre KFZ-Versicherungen vergleichen zu lassen.
Der alte Flyer wird mit hochgeladen. Bitte den Text nicht 1 zu 1 übernehmen.
Farbe und Stil sollten übernommen werden.
Die Maße für Plauderwiese:
Empfohlene Bildgröße:
1.200 x 628 Pixel
Bildseitenverhältnis: 1,91:1
Auf Grund der Zusendung von mehrerern Flyer der Designer bitte ich die Anzahl auf 3 zu einigen, d.h. bitte senden Sie für eine Plauderwiese Slidekampane 3 Flyer als ein Projekt zu. Vielen Dank für Ihre Mühe.

```html
<!DOCTYPE html>
<html lang="de">
<head>
<meta charset="utf-8">
<title>Ostwind Policenrunde – KFZ-Vergleich zu Weihnachten</title>
<link rel="stylesheet" href="https://fonts.googleapis.com/css2?family=Amatic+SC:wght@700&family=Nunito:ital,wght@0,300;0,800;1,800&display=swap">
<style>
  :root {
    --wood-light: #f6f6f4;
    --wood-shade: #e9e9e6;
    --brand-green: #9dc41e;
    --brand-green-dark: #86ad22;
    --url-green: #95c11f;
    --pine-green: #3f6b34;
    --gift-red: #c4141c;
    --ink: #3d3d3d;
    --white: #ffffff;
  }
  html, body {
    margin: 0;
    padding: 0;
    width: 1200px;
    height: 628px;
    overflow: hidden;
    background: var(--white);
  }
  .ad {
    position: relative;
    width: 1200px;
    height: 628px;
    overflow: hidden;
    font-family: "Nunito", sans-serif;
  }
  .backdrop {
    position: absolute;
    inset: 0;
    background: linear-gradient(180deg, var(--wood-light) 0%, var(--wood-shade) 100%);
  }
  .pine-garland {
    position: absolute;
    left: 0;
    right: 0;
    top: 360px;
    bottom: 0;
    background: linear-gradient(180deg, rgba(63,107,52,0) 0%, rgba(63,107,52,0.55) 35%, var(--pine-green) 75%);
  }
  .gift-box {
    position: absolute;
    inset: 0;
    width: 1200px;
    height: 628px;
  }
  .site-url {
    position: absolute;
    top: 28px;
    left: 0;
    width: 1190px;
    text-align: center;
    margin: 0;
    font-weight: 800;
    font-size: 23px;
    letter-spacing: 0.3px;
    color: var(--url-green);
  }
  .band {
    position: absolute;
    margin: 0;
    color: var(--white);
    display: flex;
    align-items: center;
    box-shadow: 0 2px 4px rgba(0,0,0,0.15);
  }
  .band--offer {
    left: 0;
    top: 95px;
    width: 723px;
    height: 44px;
    padding-left: 53px;
    box-sizing: border-box;
    background: var(--brand-green);
    font-weight: 300;
    font-size: 26px;
  }
  .band--deadline {
    left: 477px;
    top: 139px;
    width: 723px;
    height: 43px;
    padding-left: 44px;
    box-sizing: border-box;
    background: var(--brand-green-dark);
    font-weight: 800;
    font-style: italic;
    font-size: 28px;
  }
  .headline {
    position: absolute;
    left: 92px;
    top: 214px;
    margin: 0;
    font-family: "Amatic SC", cursive;
    font-weight: 700;
    font-size: 62px;
    line-height: 80px;
    letter-spacing: 2px;
    color: var(--ink);
  }
  .brand-badge {
    position: absolute;
    left: 74px;
    top: 430px;
    width: 160px;
    height: 160px;
    border-radius: 50%;
    background: var(--white);
    display: flex;
    flex-direction: column;
    align-items: center;
    justify-content: center;
    box-shadow: 0 2px 6px rgba(0,0,0,0.2);
  }
  .brand-badge__name {
    margin: 0;
    font-weight: 800;
    font-size: 17px;
    line-height: 20px;
    text-align: center;
    color: var(--url-green);
  }
  .feature-icons {
    position: absolute;
    left: 1040px;
    top: 218px;
    margin: 0;
    padding: 0;
    list-style: none;
  }
  .feature-icon {
    width: 102px;
    height: 102px;
    border-radius: 50%;
    background: var(--white);
    margin-bottom: 37px;
    display: flex;
    align-items: center;
    justify-content: center;
    box-shadow: 0 2px 6px rgba(0,0,0,0.2);
  }
  .feature-icon svg {
    width: 74px;
    height: 74px;
  }
</style>
</head>
<body>
<main class="ad">
  <div class="backdrop" role="img" aria-label="Weiße Holzdielen als Hintergrund"></div>
  <svg class="gift-box" viewBox="0 0 1200 628" role="img" aria-label="Rot verpacktes Weihnachtsgeschenk mit Schleife in der Ecke">
    <polygon points="885,135 985,0 1200,0 1200,395 925,190" fill="var(--gift-red)"/>
  </svg>
  <div class="pine-garland" role="img" aria-label="Tannenzweige mit roten Glitzerkugeln"></div>

  <p class="site-url">www.ostwind-policenrunde.de</p>
  <p class="band band--offer">Wir vergleichen für Sie Ihre KFZ-Versicherungen</p>
  <p class="band band--deadline">Vereinbaren Sie einen Termin bis zum 30.11.2018</p>

  <h1 class="headline">Schenken Sie sich doch<br>jetzt schon etwas zu Weihnachten!</h1>

  <div class="brand-badge">
    <p class="brand-badge__name">OSTWIND<br>POLICENRUNDE</p>
  </div>

  <ul class="feature-icons">
    <li class="feature-icon" aria-label="Auto">
      <svg viewBox="0 0 74 74" fill="var(--brand-green)">
        <path d="M4 40 L8 34 L24 33 L32 27 L42 28 L48 33 L66 35 L70 40 L70 44 L4 44 Z"/>
        <path d="M44 22 Q54 20 58 33" stroke="var(--brand-green)" stroke-width="3" fill="none"/>
        <circle cx="17" cy="45" r="6" fill="var(--white)" stroke="var(--brand-green)" stroke-width="3"/>
        <circle cx="56" cy="45" r="6" fill="var(--white)" stroke="var(--brand-green)" stroke-width="3"/>
      </svg>
    </li>
    <li class="feature-icon" aria-label="Geld">
      <svg viewBox="0 0 74 74" fill="none" stroke="var(--brand-green)" stroke-width="3" stroke-linejoin="round">
        <rect x="14" y="28" width="44" height="22" transform="rotate(-25 36 39)"/>
        <rect x="10" y="34" width="44" height="22" transform="rotate(-15 32 45)"/>
        <rect x="8" y="40" width="44" height="22" transform="rotate(-5 30 51)" fill="var(--brand-green)"/>
      </svg>
    </li>
    <li class="feature-icon" aria-label="Geschenk">
      <svg viewBox="0 0 74 74" fill="var(--brand-green)">
        <rect x="14" y="26" width="46" height="10"/>
        <rect x="17" y="38" width="40" height="26"/>
        <rect x="34" y="26" width="6" height="38" fill="var(--white)"/>
        <path d="M37 25 C28 10 18 18 30 24 M37 25 C46 10 56 18 44 24" stroke="var(--brand-green)" stroke-width="3" fill="none"/>
      </svg>
    </li>
  </ul>
</main>
</body>
</html>
```